Onsite Energy for Retail Tenants

Need a short one page-3 part build showing how the program for discounted clean energy works - moving into a call to action with multiple links.

1) Solar Garden Produces Energy
2) Credits Available for Tenants’ Utility Bills
3) Sign Up to Receive Utility Bill Credits.
Save 5%

This document will be used:
1) Embedded in Mailchimp emails
2) as an html landing page
3) as an image

Use the latest powerpoint Tenant slide E as guidance
Updates

Infographic is simplistic. 3 part build using graphics and information. Flow is really important so Gifs welcome.

Target Market(s)

Owners of small stores throughout the US.

Industry/Entity Type

Real Estate

Colors

Designer to choose colors to be used in the design.

Requirements
Must have
• It must explain the program clearly and succinctly using the language from the first slide of Mockup 1. This slide must become an elegant build for the 3 step process. See Mockup 2 for its cleanliness ideas for a similar but different program.
• The second slide of mockup 1 is the call to action and must have clickable links and promote trust.
• Please use the attached font styles.
• The text is sparse and so needs to be bold and in order and with the graphics needs to explain how it works perfectly.
• The graphics should be clean and sophisticated but the message and flow needs to be simple.
Nice to have
• Moving arrows to show flow of energy and credits.
• Ability to switch out language of text.

```html
<!DOCTYPE html>
<html lang="en">
<head>
<meta charset="utf-8">
<title>Clean Discount Electricity</title>
<link rel="stylesheet" href="https://fonts.googleapis.com/css2?family=Nunito:wght@300;400;600;700;800;900&display=swap">
<style>
:root{
  --orange:#d4762a;
  --orange-soft:#e9a867;
  --ink:#3b3344;
  --text:#333033;
  --muted:#5a5560;
  --page:#e6e8ea;
  --panel:#ffffff;
  --line:#c9c6c9;
}
*{box-sizing:border-box;margin:0;padding:0}
html,body{width:1200px;height:923px;overflow:hidden}
body{background:var(--page);font-family:"Nunito",sans-serif;color:var(--text);position:relative}
.panel{position:absolute;left:239px;width:722px;height:406px;background:var(--panel);box-shadow:0 4px 14px rgba(0,0,0,.18)}
.panel--how{top:41px}
.panel--offer{top:476px}
.panel__head{height:52px;background:linear-gradient(90deg,var(--orange) 0%,var(--orange) 82%,#fbe9d8 100%);display:flex;align-items:center;padding-left:17px}
.panel__title{font-weight:900;font-size:33px;color:#fff;letter-spacing:.2px;line-height:1}
.abs{position:absolute}
.num{width:37px;height:37px;border:2px solid var(--ink);border-radius:50%;display:flex;align-items:center;justify-content:center;font-weight:800;font-size:22px;color:var(--ink);transform:translate(-50%,-50%)}
.step-label{font-weight:800;font-size:15.5px;line-height:19px;color:var(--orange);text-align:center;transform:translateX(-50%);width:140px}
.chevrons{display:block}
.illus{border-radius:6px}
.illus--sun{background:radial-gradient(circle at 40% 30%,#f6c48f 0,#fbe6d1 45%,#eeecef 75%)}
.illus--house{background:linear-gradient(180deg,#fbeee2,#ecebee)}
.illus--savings{background:radial-gradient(circle at 50% 50%,#f3c79b 0,#fbeadb 55%,#fff 80%)}
.caption{font-size:14px;line-height:16.5px;color:var(--text);text-align:center;transform:translateX(-50%);width:170px}
.caption strong{color:var(--orange);font-weight:800}
.perk{display:flex;align-items:flex-start;gap:2px;font-weight:300;font-size:18px;line-height:19px;color:var(--text)}
.perk svg{flex:none;margin-top:-2px}
.step-box{width:251px;height:169px;border:2px solid var(--line);border-top:none;border-radius:14px 14px 0 0;background:#fff}
.step-box__head{height:39px;margin:0 -2px;background:var(--orange);border-radius:14px 14px 0 0;display:flex;align-items:center;justify-content:center;gap:10px;color:#fff;font-weight:900;font-size:21px;letter-spacing:.5px}
.step-box__num{width:31px;height:31px;border:2px solid #fff;border-radius:50%;display:flex;align-items:center;justify-content:center;font-size:19px}
.step-box__lead{font-weight:700;font-size:14px;line-height:16.5px;text-align:center;color:var(--text);padding:16px 10px 0}
.step-box--two .step-box__lead{padding-top:10px}
.step-box__list{list-style:none;padding:22px 0 0 8px;font-size:12.5px;line-height:19px;color:var(--orange)}
.step-box__list li::before{content:"";display:inline-block;width:7px;height:7px;background:var(--orange);margin-right:6px;vertical-align:1px}
.step-box__note{font-size:12.5px;line-height:19px;color:var(--orange);padding:13px 0 0 9px}
.btn{width:130px;height:28px;border-radius:7px;background:linear-gradient(90deg,var(--orange) 0%,var(--orange) 60%,#fbe6d2 100%);color:#fff;font-size:14.5px;font-weight:600;text-decoration:none;display:flex;align-items:center;padding-left:28px;box-shadow:0 1px 3px rgba(0,0,0,.2)}
.btn svg{position:absolute;right:8px;top:6px}
</style>
</head>
<body>

<section class="panel panel--how">
  <header class="panel__head"><h1 class="panel__title">How Clean Discount Electricity Works?</h1></header>

  <div class="abs num" style="left:113px;top:83px">1</div>
  <div class="abs num" style="left:360px;top:83px">2</div>
  <div class="abs num" style="left:601px;top:83px">3</div>

  <p class="abs step-label" style="left:113px;top:125px">Join a<br>Solar Farm</p>
  <p class="abs step-label" style="left:360px;top:113px">Receive<br>Utility Bill<br>Credits</p>
  <p class="abs step-label" style="left:601px;top:134px;text-align:left;transform:none;left:556px">Save Money</p>

  <svg class="abs chevrons" style="left:172px;top:113px" width="130" height="38" viewBox="0 0 130 38" aria-hidden="true">
    <g fill="none" stroke-width="7" stroke-linejoin="miter">
      <path d="M4 3 L20 19 L4 35" stroke="#fbe4cf"/>
      <path d="M24 3 L40 19 L24 35" stroke="#f8d3b0"/>
      <path d="M44 3 L60 19 L44 35" stroke="#f3bd8b"/>
      <path d="M64 3 L80 19 L64 35" stroke="#eca466"/>
      <path d="M84 3 L100 19 L84 35" stroke="#e08c44"/>
      <path d="M104 3 L120 19 L104 35" stroke="#d4762a"/>
    </g>
  </svg>
  <svg class="abs chevrons" style="left:414px;top:113px" width="130" height="38" viewBox="0 0 130 38" aria-hidden="true">
    <g fill="none" stroke-width="7">
      <path d="M4 3 L20 19 L4 35" stroke="#fbe4cf"/>
      <path d="M24 3 L40 19 L24 35" stroke="#f8d3b0"/>
      <path d="M44 3 L60 19 L44 35" stroke="#f3bd8b"/>
      <path d="M64 3 L80 19 L64 35" stroke="#eca466"/>
      <path d="M84 3 L100 19 L84 35" stroke="#e08c44"/>
      <path d="M104 3 L120 19 L104 35" stroke="#d4762a"/>
    </g>
  </svg>

  <div class="abs illus illus--sun" style="left:54px;top:181px;width:120px;height:120px" role="img" aria-label="Illustration of the sun shining on a row of solar panels"></div>
  <div class="abs illus illus--house" style="left:273px;top:186px;width:169px;height:110px" role="img" aria-label="Line illustration of a house between two small clouds"></div>
  <div class="abs illus illus--savings" style="left:534px;top:179px;width:130px;height:122px" role="img" aria-label="Illustration of a piggy bank with banknotes and a radiant burst"></div>

  <p class="abs caption" style="left:113px;top:313px">Solar Garden<br>Produces Energy &amp;<br>Property receives<br>Utility Credits</p>
  <p class="abs caption" style="left:360px;top:313px">Credits Available<br>for Tenants’<br>Utility Bills</p>
  <p class="abs caption" style="left:606px;top:313px">Sign Up<br>to Receive Credits<br>on your<br>Utility Bill<br><strong>Save 5%</strong></p>
</section>

<section class="panel panel--offer">
  <header class="panel__head"><h2 class="panel__title">Electricity Discount Offer</h2></header>

  <div class="abs perk" style="left:89px;top:79px">
    <svg width="36" height="36" viewBox="0 0 36 36" aria-hidden="true"><circle cx="16" cy="19" r="14" fill="none" stroke="var(--orange)" stroke-width="2.5"/><path d="M8 19 L15 27 L32 3" fill="none" stroke="var(--orange)" stroke-width="4.5" stroke-linecap="round" stroke-linejoin="round"/></svg>
    <span>Save 5%<br>on your<br>Electricity Cost</span>
  </div>
  <div class="abs perk" style="left:275px;top:79px">
    <svg width="36" height="36" viewBox="0 0 36 36" aria-hidden="true"><circle cx="16" cy="19" r="14" fill="none" stroke="var(--orange)" stroke-width="2.5"/><path d="M8 19 L15 27 L32 3" fill="none" stroke="var(--orange)" stroke-width="4.5" stroke-linecap="round" stroke-linejoin="round"/></svg>
    <span>NO Changes<br>to your Utility</span>
  </div>
  <div class="abs perk" style="left:462px;top:79px">
    <svg width="36" height="36" viewBox="0 0 36 36" aria-hidden="true"><circle cx="16" cy="19" r="14" fill="none" stroke="var(--orange)" stroke-width="2.5"/><path d="M8 19 L15 27 L32 3" fill="none" stroke="var(--orange)" stroke-width="4.5" stroke-linecap="round" stroke-linejoin="round"/></svg>
    <span>NO upfront Cost<br>or Payment</span>
  </div>

  <div class="abs step-box step-box--one" style="left:56px;top:164px">
    <div class="step-box__head">STEP <span class="step-box__num">1</span></div>
    <p class="step-box__lead">Sign Up for the<br>Electricity Discount Agreement.</p>
    <ul class="step-box__list">
      <li>It runs only for as long as you lease.</li>
      <li>Your Discount is Guaranteed</li>
    </ul>
  </div>

  <svg class="abs chevrons" style="left:306px;top:235px" width="90" height="38" viewBox="0 0 90 38" aria-hidden="true">
    <g fill="none" stroke-width="7">
      <path d="M4 3 L20 19 L4 35" stroke="#fbe4cf"/>
      <path d="M24 3 L40 19 L24 35" stroke="#f3c599"/>
      <path d="M44 3 L60 19 L44 35" stroke="#e9a063"/>
      <path d="M64 3 L80 19 L64 35" stroke="#d4762a"/>
    </g>
  </svg>

  <div class="abs step-box step-box--two" style="left:430px;top:164px">
    <div class="step-box__head">STEP <span class="step-box__num">2</span></div>
    <p class="step-box__lead">Securely Provide Brightfield Solar<br>with your Utility information<br>through MeterLink</p>
    <p class="step-box__note">We use the information only<br>to credit your bill, generate your invoice,<br>and provide clean discounted energy.</p>
  </div>

  <a class="abs btn" href="#sign-up" style="left:102px;top:348px">Sign Up
    <svg width="10" height="16" viewBox="0 0 10 16" aria-hidden="true"><path d="M2 2 L8 8 L2 14" fill="none" stroke="var(--orange)" stroke-width="2.5"/></svg>
  </a>
  <a class="abs btn" href="#contact" style="left:456px;top:348px">Contact Us
    <svg width="10" height="16" viewBox="0 0 10 16" aria-hidden="true"><path d="M2 2 L8 8 L2 14" fill="none" stroke="var(--orange)" stroke-width="2.5"/></svg>
  </a>
</section>

</body>
</html>
```